Greeting Card Design - Bright Hearts Open Pages

Hi there

Thank you for taking the time to read about this project.

The project is for a range of greeting cards for the gay and lesbian community. The brand is called "Bright Hearts Open Pages".

In this project I require four designs in total (designs for homosexual couples, two for men and two for women). The designs need to reflect the general concept of being in love.

I am looking for variety (fun and funky, as well as modern and classy - please design to your tastes and I will give feedback).

I will work with each designer closely and provide the words for the cards as the designs are developed.

Thank you for considering this project.
Updates

I'm currently having issues with the craft huddle website and it won't let me upload files to show the logo. I will do so as soon as the website allows me. Thanks

Target Market(s)

Gay and lesbian community.

Industry/Entity Type

Community

Requirements
Must have
• I am looking for variety in the range. I would like designs that are modern and classy range; and also designs that are fun and funky.
Nice to have
• Hand drawings are good for the fun range, so is colour.
The classy range can be symbolic (e.g. holding hands) or black and whites.
Should not have
• Please do not use rainbows or rainbow coloured font.

```html
<!DOCTYPE html>
<html lang="en">
<head>
<meta charset="utf-8">
<title>Bright Hearts Open Pages – My love card</title>
<link rel="stylesheet" href="https://fonts.googleapis.com/css2?family=Nothing+You+Could+Do&display=swap">
<style>
  :root {
    --paper: #ffffff;
    --page-bg: #ffffff;
    --hairline: #555555;
    --frame: #8f8279;
    --fold: #8a8a8a;
    --band-red: #be1e2d;
    --ink: #2a2a2a;
    --photo-black: #2e2e2e;
    --photo-dark: #4a4a4a;
    --photo-mid: #8c8c8c;
    --photo-light: #d6d6d6;
    --photo-pale: #e6e6e6;
  }
  * { margin: 0; padding: 0; box-sizing: border-box; }
  html, body {
    width: 799px;
    height: 1200px;
    overflow: hidden;
    background: var(--page-bg);
  }
  .sheet {
    position: absolute;
    left: 0;
    top: 0;
    width: 909px;
    height: 1365px;
    transform: scale(0.879);
    transform-origin: 0 0;
    font-family: "Nothing You Could Do", cursive;
  }

  /* Outside of the card */
  .card-outside {
    position: absolute;
    left: 21px;
    top: 26px;
    width: 867px;
    height: 630px;
    border: 1px solid var(--hairline);
    background: var(--paper);
  }
  .back-cover {
    position: absolute;
    left: 0;
    top: 0;
    width: 434px;
    height: 100%;
  }
  .front-cover {
    position: absolute;
    left: 434px;
    top: 0;
    width: 432px;
    height: 100%;
    overflow: hidden;
  }
  .cover-photo {
    position: absolute;
    inset: 0;
    background:
      radial-gradient(ellipse 38% 22% at 40% 56%, rgba(214,214,214,0.85) 0%, transparent 100%),
      radial-gradient(ellipse 30% 45% at 80% 38%, rgba(230,230,230,0.9) 0%, transparent 100%),
      radial-gradient(ellipse 30% 40% at 30% 30%, rgba(140,140,140,0.9) 0%, transparent 100%),
      radial-gradient(ellipse 55% 18% at 30% 72%, rgba(46,46,46,0.8) 0%, transparent 100%),
      linear-gradient(180deg, var(--photo-black) 0%, var(--photo-dark) 18%, var(--photo-mid) 45%, var(--photo-mid) 70%, var(--photo-light) 100%);
  }
  .title-band {
    position: absolute;
    left: 0;
    top: 491px;
    width: 300px;
    height: 83px;
    background: var(--band-red);
  }
  .cover-title {
    position: absolute;
    left: 44px;
    top: 2px;
    color: var(--paper);
    font-size: 52px;
    line-height: 1.4;
    font-weight: 400;
    white-space: nowrap;
  }
  .brand-seal {
    position: absolute;
    left: 258px;
    top: 472px;
    width: 116px;
    height: 116px;
    border-radius: 50%;
    background: var(--paper);
    display: flex;
    align-items: center;
    justify-content: center;
    text-align: center;
    padding: 12px;
  }
  .brand-name {
    color: var(--band-red);
    font-size: 16px;
    line-height: 1.15;
    font-weight: 400;
  }

  /* Inside of the card */
  .card-inside {
    position: absolute;
    left: 21px;
    top: 715px;
    width: 867px;
    height: 630px;
    background: var(--frame);
  }
  .inside-spread {
    position: absolute;
    left: 18px;
    top: 18px;
    width: 831px;
    height: 594px;
    background: var(--paper);
  }
  .fold-line {
    position: absolute;
    left: 435px;
    top: -18px;
    width: 0;
    height: 630px;
    border-left: 1.5px dashed var(--fold);
  }
  .verse {
    position: absolute;
    left: 418px;
    top: 166px;
    width: 400px;
    text-align: center;
    color: var(--ink);
    font-size: 20px;
    line-height: 54px;
  }
</style>
</head>
<body>
<main class="sheet">
  <section class="card-outside">
    <div class="back-cover"></div>
    <div class="front-cover">
      <div class="cover-photo" role="img" aria-label="Black and white photo of a male couple in shirts and ties, one embracing the other from behind as they hold hands"></div>
      <div class="title-band">
        <h1 class="cover-title">My love...</h1>
      </div>
      <div class="brand-seal">
        <span class="brand-name">Bright Hearts Open Pages</span>
      </div>
    </div>
  </section>

  <section class="card-inside">
    <div class="inside-spread">
      <div class="fold-line"></div>
      <p class="verse">
        My heart stopped wandering<br>
        When it found home with you<br>
        I love you
      </p>
    </div>
  </section>
</main>
</body>
</html>
```